Business card design needed

Business Card design required for new small plumbing business.
Would like a logo/text look that is simple and unique and does not have to be representative of a plumbing company (ie. having a cartoon plumber or toilet etc) as the companyname is self explanatory.
Would like the main colour to be green (lime green).

Industry/Entity Type

Plumber

Contact Information for Business Card

BRAMFORD PLUMBING
ABN 71 546 190 327 004

Simon Harcastle
Licensed Plumber 83615
Phone: 0487 214 670

27 Bramford Drive,
Carrowdale. 5172 Westmere

Email: bramfordplumbing@quellmail.example

Logo Text

Bramford Plumbing

Logo styles of interest
Character Logo
Wordmark Logo
Lettermark Logo

```html
<!DOCTYPE html>
<html lang="en">
<head>
<meta charset="utf-8">
<title>Bramford Plumbing — Business Card</title>
<link rel="stylesheet" href="https://fonts.googleapis.com/css2?family=Source+Sans+3:wght@400;600;700&display=swap">
<style>
  :root {
    --lime: #b5d767;
    --ink: #6b7566;
    --paper: #ffffff;
    --edge: #b9bcb6;
  }
  * { margin: 0; padding: 0; box-sizing: border-box; }
  html, body {
    width: 1200px; height: 559px; overflow: hidden;
    background: var(--paper);
    font-family: "Source Sans 3", "Myriad Pro", Arial, sans-serif;
    color: var(--ink);
  }
  .canvas { position: relative; width: 1200px; height: 559px; }
  .card { position: absolute; top: 122px; width: 549px; height: 317px; }
  .card-front { left: 34px; background: var(--lime); }
  .card-back { left: 617px; background: var(--paper); border: 1px solid var(--edge); }
  .back-band { position: absolute; left: -1px; top: -1px; width: 180px; height: 317px; background: var(--lime); }

  .line { position: absolute; white-space: nowrap; line-height: 1; }

  .front-mark { position: absolute; left: 124px; top: 103px; width: 34px; height: 34px; background: var(--ink); }
  .front-name { left: 168px; top: 138px; font-size: 29px; font-weight: 600; letter-spacing: -0.5px; }
  .front-address { left: 165px; top: 177px; font-size: 15px; }

  .back-mark { position: absolute; left: 33px; top: 42px; width: 26px; height: 26px; background: var(--paper); }
  .back-name { left: 33px; top: 93px; font-size: 13px; font-weight: 700; color: var(--paper); letter-spacing: -0.3px; }

  .person { left: 194px; top: 82px; font-size: 28px; font-weight: 700; }
  .person-role { font-size: 14px; font-weight: 400; }
  .phone { left: 195px; top: 124px; font-size: 19px; font-weight: 600; }
  .email { left: 195px; top: 144px; font-size: 18px; font-weight: 600; }
  .abn { left: 192px; top: 250px; font-size: 15px; font-weight: 600; }
  .back-address { left: 192px; top: 267px; font-size: 15px; }
</style>
</head>
<body>
<main class="canvas">
  <section class="card card-front">
    <span class="front-mark" aria-hidden="true"></span>
    <p class="line front-name">BRAMFORD PLUMBING</p>
    <p class="line front-address">Bramford Drive, Carrowdale. 5172 Westmere</p>
  </section>

  <section class="card card-back">
    <div class="back-band">
      <span class="back-mark" aria-hidden="true"></span>
      <p class="line back-name">BRAMFORD PLUMBING</p>
    </div>
    <p class="line person">Simon Harcastle <span class="person-role">- Licensed Plumber</span></p>
    <p class="line phone">0487 214 670 51 83615</p>
    <p class="line email">bramfordplumbing@quellmail.example</p>
    <p class="line abn">ABN 71 546 190 327 004</p>
    <p class="line back-address">Bramford Drive, Carrowdale. 5172 Westmere</p>
  </section>
</main>
</body>
</html>
```